Trade Show Design

Two, doublesided backdrops/one doublesided banner/one countertop. I have 3 sample pictures of the 3 items that we are purchasing and all the dimensions are listed on the file names.
website: www.brickwisestudio.net
We are a training center that teaches homeowner's how to do their own home renovations through in-person classes with hands-on training.
We are looking to update our tradeshow displays utilizing stock photos as our photos do not have high enough resolution. I have attached lots of example pictures to select from but some of my favourites that I want to use are over 10 MB so they won't upload. Will have to figure out a different way to upload. Our tagline is Learn it. Build it. Own it. We also use words such as "learn to reno" or "practical, hands-on training". We want to use our current branding (pictures of our minivan are uploaded as well) and our color palette document and really show people what we are all about - classes that people can attend so they can learn to reno their home.
Updates

For the 2 backdrops, we would like them to either be stand-alone or together incase we go to a trade show and only have room for 1 of them. They are to be different designs, front and back but a continuous flow if we are to use them together. Again, I have to figure out how to upload additional pictures as some of the ones I want to use are larger. Thanks!

Same with the Banner that is also double-sided - this is to be a different design for the back and front. We want minimal wording on everything but we really want to showcase what we do so that people can figure it out quickly when they walk by our booth....we offer in-person class with hands-on training. Learn to do by doing. Like on our vehicle that I sent example pictures of, we can put a list of a few topics so that people can understand:
Renovation Topics:
Bathroom
Drywall
Flooring
Tiling
Basement
Framing
Plumbing
Baseboards
Feature Walls

Here is the link to the Vornel Box to additional photos.

https://files.vornelbox.net/shared/7QK4r_mz2-TX8LwBnPe5YuJsdA0fGhRkZ?view=open

Thanks,
Marla

```html
<!DOCTYPE html>
<html lang="en">
<head>
<meta charset="utf-8">
<title>Brickwise Studio – Trade Show Backdrops</title>
<link href="https://fonts.googleapis.com/css2?family=Anton&family=Poppins:wght@300;500;600&display=swap" rel="stylesheet">
<style>
  :root {
    --bg: #dde3ea;
    --teal: #2a6e78;
    --teal-dark: #1f5f69;
    --cream: #e8e6b3;
    --stone: #9c9a8a;
    --sky: #b7d3ee;
    --orange: #e29a3a;
    --olive: #c8c88c;
    --white: #ffffff;
    --pill-grey: #8e8c80;
  }
  * { box-sizing: border-box; margin: 0; padding: 0; }
  html, body { width: 1200px; height: 900px; overflow: hidden; }
  body {
    background: var(--bg);
    font-family: "Poppins", sans-serif;
    display: flex;
    align-items: center;
    justify-content: center;
    gap: 26px;
  }
  .backdrop {
    width: 560px;
    height: 466px;
    display: flex;
    flex-direction: column;
    box-shadow: 0 6px 18px rgba(40, 60, 80, 0.15);
    overflow: hidden;
  }
  .photo { background: linear-gradient(135deg, #cdbfae, #8d7a66); }
  .photo--warm { background: linear-gradient(135deg, #d9d2c6, #7f6a58); }
  .photo--bright { background: linear-gradient(160deg, #eeeae4, #b79c86); }
  .photo--shop { background: linear-gradient(135deg, #6e6a62, #b89a78); }

  .cell {
    display: flex;
    flex-direction: column;
    align-items: center;
    justify-content: center;
    text-align: center;
  }
  .cell--cream { background: var(--cream); color: var(--teal-dark); }
  .cell--stone { background: var(--stone); color: var(--white); }
  .cell--sky { background: var(--sky); color: var(--teal-dark); }
  .cell--teal { background: var(--teal); color: var(--white); }

  .topics {
    font-weight: 600;
    font-size: 11px;
    line-height: 1.45;
    text-transform: uppercase;
    margin-top: 8px;
  }
  .topic-icon { width: 32px; height: 32px; }

  .brand { display: flex; align-items: center; gap: 5px; white-space: nowrap; }
  .brand__mark { width: 11px; height: 11px; background: var(--orange); flex: none; }
  .brand__name {
    font-weight: 600;
    font-size: 12.5px;
    color: var(--teal-dark);
    text-transform: uppercase;
    letter-spacing: 0.3px;
  }
  .tagline { font-weight: 300; font-size: 8px; color: var(--teal-dark); margin-top: 4px; white-space: nowrap; }

  .url-pill {
    display: flex;
    align-items: center;
    background: var(--teal);
    color: var(--white);
    border-radius: 12px;
    font-size: 9px;
    font-weight: 500;
    height: 24px;
    padding-right: 10px;
    white-space: nowrap;
  }
  .url-pill__cursor {
    width: 24px; height: 24px;
    border-radius: 50%;
    background: var(--pill-grey);
    display: flex; align-items: center; justify-content: center;
    margin-right: 8px;
    flex: none;
  }

  /* Front backdrop */
  .front__row { display: flex; }
  .front__row--top, .front__row--middle { height: 34.5%; }
  .front__row--bottom { height: 31%; }
  .front__row > .c1 { width: 26%; }
  .front__row > .c2 { width: 26%; }
  .front__row > .c3 { width: 26%; }
  .front__row > .c4 { width: 22%; }
  .front__row > .wide { width: 52%; }
  .front__row > .b1 { width: 35%; }
  .front__row > .b2 { width: 31%; }
  .front__row > .b3 { width: 34%; }
  .headline {
    font-family: "Anton", sans-serif;
    font-weight: 400;
    font-size: 46px;
    line-height: 1.05;
  }

  /* Back backdrop */
  .back { flex-direction: row; }
  .back__intro {
    width: 40%;
    background: linear-gradient(180deg, #d8d7a1, var(--olive) 60%, #b5b67b);
    display: flex;
    flex-direction: column;
    align-items: center;
    padding: 52px 12px 24px;
  }
  .back__headline {
    font-family: "Anton", sans-serif;
    font-weight: 400;
    color: var(--teal-dark);
    font-size: 34px;
    line-height: 1.15;
    text-align: center;
    margin-top: 60px;
  }
  .back__headline .pill {
    display: inline-block;
    background: var(--pill-grey);
    color: var(--white);
    padding: 0 8px;
    border-radius: 6px;
    transform: rotate(-2deg);
  }
  .back__underline { width: 110px; height: 10px; margin-top: 2px; }
  .back__url { margin-top: auto; }
  .back__grid { width: 60%; display: flex; flex-direction: column; }
  .back__row { display: flex; }
  .back__row--top { height: 34%; }
  .back__row--mid { height: 34%; }
  .back__row--bottom { height: 32%; }
  .back__row--top > :first-child { width: 53%; }
  .back__row--top > :last-child { width: 47%; }
  .back__row--mid > * { width: 100%; }
  .back__row--bottom > :first-child { width: 53%; }
  .back__row--bottom > :last-child { width: 47%; }
  .back .topics { font-size: 10px; }
</style>
</head>
<body>

<!-- Front backdrop -->
<section class="backdrop front">
  <div class="front__row front__row--top">
    <div class="c1 photo" role="img" aria-label="Smiling couple in work shirts and tool belts, one holding a cordless drill"></div>
    <div class="c2 cell cell--cream">
      <div class="brand"><span class="brand__mark"></span><span class="brand__name">Brickwise Studio</span></div>
      <p class="tagline">Learn it. Build it. Own it.</p>
    </div>
    <div class="c3 photo photo--warm" role="img" aria-label="Smiling woman in a plaid shirt swinging a hammer toward the camera"></div>
    <div class="c4 cell cell--stone">
      <svg class="topic-icon" viewBox="0 0 40 40" aria-hidden="true">
        <rect x="6" y="8" width="20" height="10" rx="2" fill="#fff"/>
        <rect x="26" y="11" width="10" height="4" fill="#fff"/>
        <rect x="11" y="18" width="8" height="12" fill="#fff"/>
        <rect x="9" y="30" width="12" height="5" rx="1" fill="#fff"/>
      </svg>
      <p class="topics">Drywall<br>Feature Walls<br>Framing</p>
    </div>
  </div>
  <div class="front__row front__row--middle">
    <div class="c1 cell cell--cream">
      <svg class="topic-icon" viewBox="0 0 40 40" aria-hidden="true">
        <path d="M8 36 V12 a8 8 0 0 1 16 0" fill="none" stroke="#1f5f69" stroke-width="3"/>
        <path d="M16 16 a10 10 0 0 1 16 0 Z" fill="#1f5f69"/>
        <g stroke="#1f5f69" stroke-width="1.5"><line x1="18" y1="20" x2="16" y2="26"/><line x1="22" y1="20" x2="21" y2="28"/><line x1="26" y1="20" x2="27" y2="28"/><line x1="30" y1="20" x2="33" y2="26"/></g>
      </svg>
      <p class="topics">Tiling<br>Bathroom<br>Plumbing</p>
    </div>
    <div class="wide cell cell--teal">
      <h1 class="headline">Learn<br>To Reno</h1>
      <svg width="150" height="16" viewBox="0 0 150 16" aria-hidden="true">
        <path d="M2 10 Q60 4 146 6 Q110 8 80 14" fill="none" stroke="var(--orange)" stroke-width="2.2" stroke-linecap="round"/>
      </svg>
    </div>
    <div class="c4 cell cell--sky">
      <svg class="topic-icon" viewBox="0 0 40 40" aria-hidden="true">
        <rect x="6" y="20" width="28" height="14" rx="2" fill="#1f5f69"/>
        <rect x="12" y="6" width="4" height="16" fill="#1f5f69"/>
        <rect x="20" y="10" width="4" height="12" fill="#1f5f69"/>
        <rect x="10" y="25" width="20" height="3" fill="#b7d3ee"/>
      </svg>
      <p class="topics">Flooring<br>Baseboards<br>Basement</p>
    </div>
  </div>
  <div class="front__row front__row--bottom">
    <div class="b1 photo photo--bright" role="img" aria-label="Couple in a bright room holding a paint roller and wall panel"></div>
    <div class="b2 cell cell--cream">
      <div class="url-pill">
        <span class="url-pill__cursor">
          <svg width="9" height="11" viewBox="0 0 9 11" aria-hidden="true"><path d="M1 1 L1 10 L3.5 7.5 L5.5 10.5 L7 9.5 L5 6.5 L8 6.5 Z" fill="#fff"/></svg>
        </span>brickwisestudio.net
      </div>
    </div>
    <div class="b3 photo photo--shop" role="img" aria-label="Woman in safety glasses driving a screw with a cordless drill in a workshop"></div>
  </div>
</section>

<!-- Back backdrop -->
<section class="backdrop back">
  <div class="back__intro" role="img" aria-label="Faded olive-toned photo of a woman working with a power tool, behind the headline">
    <div class="brand"><span class="brand__mark"></span><span class="brand__name">Brickwise Studio</span></div>
    <p class="tagline">Learn it. Build it. Own it.</p>
    <h2 class="back__headline">Practical,<br><span class="pill">Hands-on</span><br>Training.</h2>
    <svg class="back__underline" viewBox="0 0 120 10" aria-hidden="true">
      <path d="M2 6 Q60 2 118 5" fill="none" stroke="var(--orange)" stroke-width="2" stroke-linecap="round"/>
    </svg>
    <div class="url-pill back__url">
      <span class="url-pill__cursor">
        <svg width="9" height="11" viewBox="0 0 9 11" aria-hidden="true"><path d="M1 1 L1 10 L3.5 7.5 L5.5 10.5 L7 9.5 L5 6.5 L8 6.5 Z" fill="#fff"/></svg>
      </span>brickwisestudio.net
    </div>
  </div>
  <div class="back__grid">
    <div class="back__row back__row--top">
      <div class="cell cell--teal">
        <svg class="topic-icon" viewBox="0 0 40 40" aria-hidden="true">
          <rect x="6" y="8" width="20" height="10" rx="2" fill="#fff"/>
          <rect x="26" y="11" width="10" height="4" fill="#fff"/>
          <rect x="11" y="18" width="8" height="12" fill="#fff"/>
          <rect x="9" y="30" width="12" height="5" rx="1" fill="#fff"/>
        </svg>
        <p class="topics">Drywall<br>Feature Walls<br>Framing</p>
      </div>
      <div class="cell cell--cream">
        <svg class="topic-icon" viewBox="0 0 40 40" aria-hidden="true">
          <rect x="6" y="20" width="28" height="14" rx="2" fill="#1f5f69"/>
          <rect x="12" y="6" width="4" height="16" fill="#1f5f69"/>
          <rect x="20" y="10" width="4" height="12" fill="#1f5f69"/>
          <rect x="10" y="25" width="20" height="3" fill="#e8e6b3"/>
        </svg>
        <p class="topics">Flooring<br>Baseboards<br>Basement</p>
      </div>
    </div>
    <div class="back__row back__row--mid">
      <div class="photo photo--bright" role="img" aria-label="Couple installing a ceiling light fixture together"></div>
    </div>
    <div class="back__row back__row--bottom">
      <div class="photo photo--warm" role="img" aria-label="Couple kneeling to lay a floor board"></div>
      <div class="cell cell--sky">
        <svg class="topic-icon" viewBox="0 0 40 40" aria-hidden="true">
          <path d="M8 36 V12 a8 8 0 0 1 16 0" fill="none" stroke="#1f5f69" stroke-width="3"/>
          <path d="M16 16 a10 10 0 0 1 16 0 Z" fill="#1f5f69"/>
          <g stroke="#1f5f69" stroke-width="1.5"><line x1="18" y1="20" x2="16" y2="26"/><line x1="22" y1="20" x2="21" y2="28"/><line x1="26" y1="20" x2="27" y2="28"/><line x1="30" y1="20" x2="33" y2="26"/></g>
        </svg>
        <p class="topics">Tiling<br>Bathroom<br>Plumbing</p>
      </div>
    </div>
  </div>
</section>

</body>
</html>
```